Elegant Business Card for Technology Company

Client is a supplier of innovative industrial communications and automation equipment since 2002. This contest is to gather fresh ideas for a redesign of the existing business card. Client is looking for design that best communicates tagline "Industrial Networking and Computing Specialist".

Design submissions should look modern, clean, elegant and professional. It should not be cluttered. Use white as the primary colour. Orange and black as secondary colour. Refer to jpeg File 1 on the current design.

Fonts used by Client used include Arial Regular, Arial Black, Roboto Regular, Roboto Black and Lato.

The winning design will be sent for offset printing using super white 250gsm artcard paper (open for suggestions).

Target Market(s)

System Engineers, Project Managers, Purchasing Managers from companies providing engineering services for Smart Cities.

Industry/Entity Type

Information Technology

Contact Information for Business Card

Refer to PDF File 3 for Business Card Details. Priority of short contact information would be as follows Name > Job Title > Email > Mobile > Web > Tel > Fax > Business Address >UEN (UEN represents company registration number)

Font styles to use
Sans Serif

Colors
ffffff
f37122
000000
5c5c5c

Requirements
Must have
• Refer to AI File 2 (Company Logo) & PDF File 3 (Information on Namecard)
Should not have
• No QR codes
• No Social Media Icons
• Do not create full Black or Orange colour background

```html
<!DOCTYPE html>
<html lang="en">
<head>
<meta charset="utf-8">
<title>QLX Business Card</title>
<link rel="stylesheet" href="https://fonts.googleapis.com/css2?family=Roboto:wght@400;500;900&display=swap">
<style>
  :root {
    --white: #ffffff;
    --orange: #f37122;
    --black: #000000;
    --ink: #141414;
    --grey: #5c5c5c;
    --backdrop: #e9e6e1;
  }
  * { margin: 0; padding: 0; box-sizing: border-box; }
  html, body {
    width: 1200px; height: 950px; overflow: hidden;
    background: var(--backdrop);
    font-family: "Roboto", Arial, sans-serif;
  }
  .card {
    position: absolute;
    width: 620px; height: 354px;
    border-radius: 4px;
    box-shadow: 0 10px 30px rgba(0,0,0,.18);
    overflow: hidden;
  }
  /* Back of card */
  .card-back {
    left: 90px; top: 90px;
    background: linear-gradient(135deg, #1c1c1c 0%, var(--ink) 60%, #080808 100%);
    color: var(--white);
  }
  .card-back .brand-name {
    position: absolute; left: 150px; top: 70px;
    font-weight: 900; font-size: 96px; letter-spacing: 2px;
    color: var(--white); line-height: 1;
  }
  .card-back .services {
    position: absolute; right: 60px; top: 190px;
    list-style: none; text-align: right;
    font-size: 15px; line-height: 22px; color: var(--white);
  }
  /* Front of card */
  .card-front {
    left: 490px; top: 500px;
    background: var(--white);
  }
  .card-front .swoosh { position: absolute; inset: 0; }
  .brand-lockup {
    position: absolute; left: 325px; top: 62px;
    display: flex; align-items: center; gap: 14px;
  }
  .brand-lockup .brand-dot {
    width: 70px; height: 70px; border-radius: 50%;
    background: var(--orange);
  }
  .brand-lockup .brand-name {
    font-weight: 900; font-size: 72px; letter-spacing: 2px;
    color: var(--black); line-height: 1;
  }
  .person {
    position: absolute; right: 36px; top: 160px; text-align: right;
  }
  .person .name { font-size: 20px; font-weight: 500; color: var(--orange); }
  .person .title { font-size: 14px; color: var(--grey); margin-top: 2px; }
  .contacts {
    position: absolute; left: 36px; top: 178px;
    list-style: none; color: var(--white);
    font-size: 14.5px; line-height: 21px;
  }
  .contacts li { display: flex; align-items: center; gap: 9px; }
  .contacts svg { width: 13px; height: 13px; flex: none; fill: var(--white); }
  .contacts .address { padding-left: 22px; }
</style>
</head>
<body>

<section class="card card-back" aria-label="Business card back">
  <div class="brand-name">QLX</div>
  <ul class="services">
    <li>Industrial Networking &amp; Computing Specialist</li>
    <li>Industrial Ethernet / Wireless / Cellular</li>
    <li>Industrial &amp; Embedded Computing / Serial / Fieldbus Connectivity</li>
    <li>IP Video Surveillance / Remote Automation</li>
  </ul>
</section>

<section class="card card-front" aria-label="Business card front">
  <svg class="swoosh" width="620" height="354" viewBox="0 0 620 354" aria-hidden="true">
    <path d="M0,132 C170,88 440,150 590,354 L575,354 C430,160 170,102 0,146 Z" fill="var(--black)"/>
    <path d="M0,146 C170,102 430,160 575,354 L0,354 Z" fill="var(--orange)"/>
  </svg>

  <div class="brand-lockup">
    <span class="brand-dot"></span>
    <span class="brand-name">QLX</span>
  </div>

  <div class="person">
    <div class="name">Darren Lim</div>
    <div class="title">Sales Manager</div>
  </div>

  <ul class="contacts">
    <li><svg viewBox="0 0 16 16"><path d="M3 1l3 3-2 2c1 2 3 4 5 5l2-2 3 3-2 3C6 15 1 10 0 3z"/></svg>+65 6100 2040</li>
    <li><svg viewBox="0 0 16 16"><path d="M4 0h8v16H4zM5.5 2v10h5V2z"/></svg>+65 8100 3050</li>
    <li><svg viewBox="0 0 16 16"><path d="M4 1h7v4H4zM1 6h14v8H1zM4 12h8v-2H4z"/></svg>+65 6100 2041</li>
    <li><svg viewBox="0 0 16 16"><path d="M0 3h16v10H0zM1.5 4.5L8 9l6.5-4.5z"/></svg>sales@qlxsystems.sg</li>
    <li><svg viewBox="0 0 16 16"><circle cx="8" cy="8" r="7"/></svg>www.qlxsystems.sg</li>
    <li class="address">22 Kallang Way</li>
    <li class="address">Tech Hub #05-12 (Lobby B)</li>
    <li class="address">Singapore 349201</li>
  </ul>
</section>

</body>
</html>
```